Home Remodeler Needs a Website!

Single page (plus contact form) website for small home remodeling company. He's got a few pictures he'd like on the site and needs some basic text. He likes clean, simple designs and is "more traditional" in his stylistic preferences. Most of his business comes from word-of-mouth advertising and so the site is just something he needs for people to feel more comfortable with his business.

Target Market(s)

People who want to remodel their homes

Coding

Coded - Design and coding required

Number of Pages Required

2 page

Requirements
Must have
• Main page to include some or all of the attached images, contact page. Neutral colors. Old domain: lindcroftmeadowbuild.com New domain: qm-ventureworks.com You can pull text from the old site or update it.
Should not have
• No loud colors/loud visual elements

```html
<!DOCTYPE html>
<html lang="en">
<head>
<meta charset="utf-8">
<title>Lindcroft Meadow Build</title>
<link rel="stylesheet" href="https://fonts.googleapis.com/css2?family=Montserrat:wght@600;700;800&family=Open+Sans:wght@400;600;700&display=swap">
<style>
:root{
  --accent:#b4945a;
  --accent-light:#d6c39a;
  --accent-pale:#e8dcc2;
  --band:#7a7062;
  --band-deep:#6c6356;
  --ink:#1c1c1c;
  --text:#2a2a2a;
  --muted:#6b6b6b;
  --white:#ffffff;
  --line:#3c3c3c;
}
*{box-sizing:border-box;margin:0;padding:0}
html,body{width:1200px;height:3691px;overflow:hidden}
body{font-family:"Open Sans",Arial,sans-serif;color:var(--text);background:var(--white);position:relative}
.abs{position:absolute}
.heading{font-family:"Montserrat",Arial,sans-serif;font-weight:800;font-size:35px;letter-spacing:.5px;text-transform:uppercase;color:var(--ink);white-space:nowrap}
.heading .accent{color:var(--accent)}
.btn{display:inline-flex;align-items:center;justify-content:center;background:var(--accent);color:var(--white);font-weight:700;font-size:15px;text-transform:uppercase;white-space:nowrap}

/* top bar */
.topbar{top:0;left:0;width:1200px;height:48px;background:var(--ink);color:var(--white);font-size:15px}
.topbar .contact{left:110px;top:0;height:48px;display:flex;align-items:center;gap:14px}
.topbar .contact span{display:flex;align-items:center;gap:10px}
.topbar .social{right:112px;top:18px;display:flex;gap:9px}
.dot{width:12px;height:12px;background:var(--accent);border-radius:2px}

/* nav */
.nav{top:48px;left:0;width:1200px;height:78px;background:var(--white)}
.brand{left:112px;top:24px;font-weight:700;font-size:22px;color:var(--ink);white-space:nowrap}
.menu{left:431px;top:29px;display:flex;gap:24px;font-size:15px;color:var(--ink)}
.menu .active{color:var(--accent)}
.nav .btn{left:956px;top:17px;width:132px;height:45px}

/* hero */
.hero{top:126px;left:0;width:1200px;height:600px;background:linear-gradient(120deg,#d9d2c7 0%,#efe9df 35%,#c9c2b6 60%,#3a3f4e 85%,#2c3140 100%)}
.hero-box{left:301px;top:189px;width:598px;height:129px;background:rgba(55,50,45,.55)}
.hero h1{position:absolute;top:211px;left:0;width:1200px;text-align:center;font-family:"Montserrat",Arial,sans-serif;font-weight:700;font-size:26px;color:var(--white);white-space:nowrap}
.hero h1 span{color:var(--accent-light)}
.hero p{position:absolute;top:253px;left:0;width:1200px;text-align:center;font-size:17px;line-height:26px;color:var(--white)}
.hero .btn{left:534px;top:319px;width:132px;height:45px}
.dots{left:569px;top:565px;display:flex;gap:5px}
.dots i{width:11px;height:11px;border:1.5px solid var(--white)}
.dots i.on{background:var(--accent-light);border-color:var(--accent-light)}

/* about */
.about .heading{left:110px;top:812px}
.about-text{left:110px;top:870px;width:491px;font-size:15px;line-height:25px;color:var(--muted);text-align:justify}
.about-text p+p{margin-top:14px}
.about .btn{left:111px;top:1112px;width:134px;height:47px}
.about-frame{left:679px;top:821px;width:410px;height:334px;background:var(--white);box-shadow:0 2px 10px rgba(0,0,0,.18);padding:5px}
.about-photo{width:100%;height:100%;background:linear-gradient(150deg,#8b9aa0,#5c6a6e 55%,#3a3f40);position:relative}
.about-photo::after{content:"";position:absolute;inset:12px;border:1px solid rgba(255,255,255,.7)}

/* why choose */
.why{top:1250px;left:0;width:1200px;height:666px;background:linear-gradient(180deg,#f6f6f6,#ebebeb)}
.why .heading{top:40px;left:0;width:1200px;text-align:center}
.feature{width:300px;text-align:center}
.badge{width:118px;height:118px;border-radius:50%;background:radial-gradient(circle,var(--white) 0 46px,var(--accent) 47px 52px,var(--accent-pale) 53px 59px);margin:0 auto;display:flex;align-items:center;justify-content:center}
.feature h3{font-weight:400;font-size:19px;color:var(--ink);margin-top:16px;white-space:nowrap}
.feature p{font-size:14px;line-height:23px;color:var(--muted);margin-top:14px}

/* services */
.services{top:1916px;left:0;width:1200px;height:600px;background:linear-gradient(180deg,var(--band),var(--band-deep))}
.services .heading{top:30px;left:0;width:1200px;text-align:center;color:var(--white)}
.card{top:107px;width:310px;height:360px;background:var(--white);padding:4px}
.card-photo{height:206px}
.card h3{font-weight:400;font-size:21px;color:var(--ink);margin:16px 0 0 11px;white-space:nowrap}
.card p{font-size:14px;line-height:22px;color:var(--muted);margin:8px 11px 0}
.card a{display:flex;align-items:center;gap:8px;font-size:15px;font-weight:600;color:var(--accent);margin:8px 0 0 11px;text-decoration:none}
.services .outline{left:513px;top:515px;width:176px;height:46px;border:2px solid var(--white);color:var(--white);font-weight:700;font-size:14px;display:flex;align-items:center;justify-content:center}

/* projects */
.projects .heading{top:2600px;left:0;width:1200px;text-align:center}

/* footer */
.footer{top:3318px;left:0;width:1200px;height:373px;background:var(--ink);color:var(--white);font-size:14px}
.footer h4{font-weight:600;font-size:18px}
.footer .brand-name{font-weight:700;font-size:19px;white-space:nowrap}
.f-row{display:flex;align-items:center;gap:15px;line-height:26px}
.hours td{padding:0 24px 0 0;line-height:24px}
.rule{left:110px;width:978px;height:1px;background:var(--line)}
.f-menu{left:456px;top:254px;display:flex;gap:40px;font-size:16px;font-weight:600;text-transform:uppercase}
.f-social{left:110px;top:259px;display:flex;gap:10px}
.copy{left:110px;top:323px;font-size:12px}
.legal{right:112px;top:323px;font-size:12px;display:flex;gap:10px}
</style>
</head>
<body>

<header>
  <div class="abs topbar">
    <div class="abs contact">
      <span><svg width="13" height="13" viewBox="0 0 24 24"><path fill="#b4945a" d="M6.6 10.8a15 15 0 006.6 6.6l2.2-2.2c.3-.3.7-.4 1-.2 1.1.4 2.3.6 3.6.6.6 0 1 .4 1 1V20c0 .6-.4 1-1 1A17 17 0 013 4c0-.6.4-1 1-1h3.5c.6 0 1 .4 1 1 0 1.3.2 2.5.6 3.6.1.3 0 .7-.2 1z"/></svg>555-318-2046</span>
      <span style="margin:0 10px">|</span>
      <span><svg width="15" height="12" viewBox="0 0 24 18"><rect width="24" height="18" rx="2" fill="#b4945a"/><path d="M1 2l11 8 11-8" stroke="#1c1c1c" stroke-width="2" fill="none"/></svg>owen@lindcroftmeadowbuild.com</span>
    </div>
    <div class="abs social"><i class="dot"></i><i class="dot"></i><i class="dot"></i><i class="dot"></i><i class="dot"></i></div>
  </div>

  <nav class="abs nav">
    <div class="abs brand">Lindcroft Meadow Build</div>
    <div class="abs menu"><span class="active">Home</span><span>About Us</span><span>Products</span><span>Extras</span><span>Resources</span><span>Blog</span></div>
    <div class="abs btn">Contact Us</div>
  </nav>
</header>

<section class="abs hero" role="img" aria-label="Bright remodeled kitchen with white cabinets, navy island and brass pendant lights">
  <div class="abs hero-box"></div>
  <h1>WELCOME TO <span>LINDCROFT MEADOW BUILD</span></h1>
  <p>When you want affordable, quality home construction<br>services; think of us to do the job.</p>
  <div class="abs btn">Get Started</div>
  <div class="abs dots"><i></i><i class="on"></i><i></i><i></i></div>
</section>

<section class="about">
  <h2 class="abs heading"><span class="accent">About</span> Us</h2>
  <div class="abs about-text">
    <p>With over 20 years experience in residential and commercial construction, you can trust your project to Lindcroft Meadow Build.</p>
    <p>I have built my business with a partnership of clients, employees, subcontractors, suppliers and inspectors. Since each project is unique, this partnership brings creative ideas to your home. I have deep "hands on" history in construction from foundations to final finishing touches. We cultivate suppliers who deliver quality materials on time and without damage.</p>
  </div>
  <div class="abs btn">Learn More</div>
  <div class="abs about-frame"><div class="about-photo" role="img" aria-label="Remodeled bathroom with soaking tub, tiled walls and skylight"></div></div>
</section>

<section class="abs why">
  <h2 class="abs heading"><span class="accent">Why</span> Choose Us</h2>

  <div class="abs feature" style="left:109px;top:116px">
    <div class="badge"><svg width="48" height="48" viewBox="0 0 48 48" fill="none" stroke="#1c1c1c" stroke-width="2"><path d="M6 24L24 9l18 15M11 20v20h26V20"/><rect x="20" y="28" width="8" height="12"/></svg></div>
    <h3>Pre Construction Consultation</h3>
    <p>Lorem ipsum dolor sit amet, consectetur adi piscing elit, sed do eiusmod tempor incididunt ut labore et</p>
  </div>
  <div class="abs feature" style="left:450px;top:116px">
    <div class="badge"><svg width="46" height="46" viewBox="0 0 46 46" fill="none" stroke="#1c1c1c" stroke-width="2"><rect x="6" y="6" width="34" height="34"/><path d="M12 14h12v10H12zM28 14h6M28 20h6M12 30h22"/></svg></div>
    <h3>New Construction</h3>
    <p>Lorem ipsum dolor sit amet, consectetur adi piscing elit, sed do eiusmod tempor incididunt ut labore et</p>
  </div>
  <div class="abs feature" style="left:789px;top:116px">
    <div class="badge"><svg width="48" height="48" viewBox="0 0 48 48" fill="none" stroke="#1c1c1c" stroke-width="2"><rect x="8" y="24" width="32" height="16"/><path d="M8 30h32M16 24V14h6v10M30 24V10M26 16h8"/></svg></div>
    <h3>Remodeling Kitchens &amp; Baths</h3>
    <p>Lorem ipsum dolor sit amet, consectetur adi piscing elit, sed do eiusmod tempor incididunt ut labore et</p>
  </div>

  <div class="abs feature" style="left:109px;top:386px">
    <div class="badge"><svg width="46" height="46" viewBox="0 0 46 46" fill="none" stroke="#1c1c1c" stroke-width="2.5"><rect x="8" y="6" width="18" height="34"/><path d="M13 13h3M19 13h3M13 20h3M19 20h3M13 27h3M19 27h3M30 30h10M35 25v10"/></svg></div>
    <h3>Additions</h3>
    <p>Lorem ipsum dolor sit amet, consectetur adi piscing elit, sed do eiusmod tempor incididunt ut labore et</p>
  </div>
  <div class="abs feature" style="left:450px;top:386px">
    <div class="badge"><svg width="46" height="46" viewBox="0 0 46 46" fill="none" stroke="#1c1c1c" stroke-width="2"><path d="M8 18Q23 4 38 18zM23 18v20M10 32h26l-4 6H14z"/></svg></div>
    <h3>Porches &amp; Decks</h3>
    <p>Lorem ipsum dolor sit amet, consectetur adi piscing elit, sed do eiusmod tempor incididunt ut labore et</p>
  </div>
  <div class="abs feature" style="left:789px;top:386px">
    <div class="badge"><svg width="48" height="48" viewBox="0 0 48 48" fill="none" stroke="#1c1c1c" stroke-width="2"><rect x="6" y="16" width="36" height="24"/><path d="M10 16v-6M24 16V8M38 16v-6M11 22h4v5h-4zM22 22h4v5h-4zM33 22h4v5h-4zM11 31h4v5h-4zM33 31h4v5h-4zM21 40v-8h6v8"/></svg></div>
    <h3>Historic Renovations</h3>
    <p>Lorem ipsum dolor sit amet, consectetur adi piscing elit, sed do eiusmod tempor incididunt ut labore et</p>
  </div>
</section>

<section class="abs services">
  <h2 class="abs heading">Our Services</h2>

  <article class="abs card" style="left:112px">
    <div class="card-photo" role="img" aria-label="Installers fitting a new window" style="background:linear-gradient(135deg,#c9d4d6,#8aa08c 60%,#3d4a3a)"></div>
    <h3>Window Replacement</h3>
    <p>Sed ut perspiciatis unde omnis istenat us error sit voluptatem accusantium dolore mque laudantium.</p>
    <a>Learn More <svg width="13" height="13" viewBox="0 0 14 14" fill="none" stroke="#b4945a" stroke-width="1.6"><circle cx="7" cy="7" r="6"/><path d="M4 7h6M7.5 4.5L10 7l-2.5 2.5"/></svg></a>
  </article>
  <article class="abs card" style="left:445px">
    <div class="card-photo" role="img" aria-label="Technician servicing a wall-mounted air conditioner" style="background:linear-gradient(135deg,#e8e8e8,#c9c9cc 55%,#4a5f8a)"></div>
    <h3>Air Conditioning</h3>
    <p>Sed ut perspiciatis unde omnis istenat us error sit voluptatem accusantium dolore mque laudantium.</p>
    <a>Learn More <svg width="13" height="13" viewBox="0 0 14 14" fill="none" stroke="#b4945a" stroke-width="1.6"><circle cx="7" cy="7" r="6"/><path d="M4 7h6M7.5 4.5L10 7l-2.5 2.5"/></svg></a>
  </article>
  <article class="abs card" style="left:779px">
    <div class="card-photo" role="img" aria-label="Roofers installing metal roof panels" style="background:linear-gradient(160deg,#6f8096,#b9c2cf 55%,#e6e9ee)"></div>
    <h3>Roofing</h3>
    <p>Sed ut perspiciatis unde omnis istenat us error sit voluptatem accusantium dolore mque laudantium.</p>
    <a>Learn More <svg width="13" height="13" viewBox="0 0 14 14" fill="none" stroke="#b4945a" stroke-width="1.6"><circle cx="7" cy="7" r="6"/><path d="M4 7h6M7.5 4.5L10 7l-2.5 2.5"/></svg></a>
  </article>

  <div class="abs outline">VIEW ALL SERVICES</div>
</section>

<section class="projects">
  <h2 class="abs heading"><span class="accent">Our</span> Latest Projects</h2>
  <div class="abs" role="img" aria-label="Open kitchen and dining area with white cabinets" style="left:110px;top:2694px;width:476px;height:248px;background:linear-gradient(135deg,#d8dde0,#b8aa97 55%,#5b4a3a)"></div>
  <div class="abs" role="img" aria-label="Wooden deck with outdoor seating among pine trees at sunset" style="left:611px;top:2694px;width:476px;height:248px;background:linear-gradient(180deg,#c9ad7a,#4f5a3a 45%,#8a5d3b)"></div>
  <div class="abs" role="img" aria-label="Kitchen with stainless refrigerator and dark cabinets" style="left:110px;top:2958px;width:311px;height:267px;background:linear-gradient(135deg,#35496a,#8a8f92 50%,#3d2c22)"></div>
  <div class="abs" role="img" aria-label="Roof edge with gutter and wood siding" style="left:442px;top:2958px;width:311px;height:267px;background:linear-gradient(160deg,#aebed6,#2a2a2a 50%,#b07a38)"></div>
  <div class="abs" role="img" aria-label="Dark wood home bar with pendant light" style="left:775px;top:2958px;width:312px;height:267px;background:linear-gradient(160deg,#3a2a22,#6b4630 50%,#121010)"></div>
</section>

<footer class="abs footer">
  <div class="abs" style="left:110px;top:46px">
    <div class="brand-name">Lindcroft Meadow Build</div>
    <div style="margin-top:20px">
      <div class="f-row"><svg width="13" height="13" viewBox="0 0 24 24"><path fill="#b4945a" d="M6.6 10.8a15 15 0 006.6 6.6l2.2-2.2c.3-.3.7-.4 1-.2 1.1.4 2.3.6 3.6.6.6 0 1 .4 1 1V20c0 .6-.4 1-1 1A17 17 0 013 4c0-.6.4-1 1-1h3.5c.6 0 1 .4 1 1 0 1.3.2 2.5.6 3.6.1.3 0 .7-.2 1z"/></svg>&nbsp;&nbsp;555-318-2046</div>
      <div class="f-row"><svg width="14" height="14" viewBox="0 0 24 24"><rect x="2" y="6" width="20" height="15" rx="2" fill="#b4945a"/><rect x="6" y="2" width="12" height="6" fill="#b4945a"/></svg>&nbsp;&nbsp;555-318-2097</div>
    </div>
  </div>

  <div class="abs" style="left:454px;top:46px">
    <h4>Business Hours</h4>
    <table class="hours" style="margin-top:16px;border-collapse:collapse">
      <tr><td>Monday - Friday</td><td>7:00 am - 6:00 pm</td></tr>
      <tr><td>Saturday</td><td>Closed</td></tr>
      <tr><td>Sunday</td><td>Closed</td></tr>
    </table>
  </div>

  <div class="abs" style="left:821px;top:46px">
    <h4>Company</h4>
    <div style="display:flex;gap:22px;margin-top:16px;line-height:24px">
      <svg width="12" height="16" viewBox="0 0 12 16" style="margin-top:4px"><path fill="#b4945a" d="M6 0a6 6 0 00-6 6c0 4.5 6 10 6 10s6-5.5 6-10a6 6 0 00-6-6zm0 8.2A2.2 2.2 0 116 3.8a2.2 2.2 0 010 4.4z"/></svg>
      <div>Lindcroft Meadow Build<br>Box 40517<br>Ashford, TN 37008</div>
    </div>
    <div style="display:flex;gap:20px;margin-top:10px;align-items:center">
      <svg width="15" height="11" viewBox="0 0 24 18" fill="none" stroke="#b4945a" stroke-width="2"><rect x="1" y="1" width="22" height="16" rx="1"/><path d="M1 2l11 8 11-8"/></svg>
      <span>owen@lindcroftmeadowbuild.com</span>
    </div>
  </div>

  <div class="abs rule" style="top:231px"></div>
  <div class="abs f-social"><i class="dot"></i><i class="dot"></i><i class="dot"></i><i class="dot"></i><i class="dot"></i></div>
  <div class="abs f-menu"><span>Home</span><span>About Us</span><span>Products</span><span>Extras</span><span>Resources</span><span>Blog</span></div>
  <div class="abs rule" style="top:302px"></div>
  <div class="abs copy">© Copyrights &nbsp;2021 Lindcroft Meadow Build. All rights reserved</div>
  <div class="abs legal"><span>Privacy Policy</span><span>|</span><span>Terms Of Conditions</span></div>
</footer>

</body>
</html>
```